Forensic Document Examiner, looking for contemporary update to my stationery design.

Looking for professional, classy logo design for stationery and business cards. My current stationery and business card is attached.I believe a logo image makes a header section interesting, so an intriguing design of a pen, feathered pen, microscope, magnifying glass, etc., would be appropriate. I have been in the business for over 30 years. I leave ideas to the imagination of the designer.My work involves mainly, the comparison of signatures and handwriting. I also resolve alterations, obliterations, and work as shown on my website: www.documentexaminer.infoThe image produced will be printed on quality white stationery and envelopes. The stationery will be photocopied by my clients, so the images should be reproducible. The business cards may be designed in other than white.

Target Market(s)

Attorneys

Font styles to use
Sans Serif

Colors

Designer to choose colors to be used in the design.

Requirements
Must have
• Image suitable for white stationery and photocopying.
• Classy logo and image; no casual fonts.
Nice to have
• Intriguing, contemporary design incorporating a relevant logo to my work.

```html
<!DOCTYPE html>
<html lang="en">
<head>
<meta charset="utf-8">
<title>Martin R. Hale – Business Card</title>
<link rel="stylesheet" href="https://fonts.googleapis.com/css2?family=Open+Sans:ital,wght@0,400;0,600;0,700;1,400&display=swap">
<style>
  :root {
    --page: #ecebe8;
    --card-dark: #2d2d2d;
    --card-dark-edge: #1f1f1f;
    --band-blue: #3232a0;
    --band-blue-deep: #23226a;
    --accent-yellow: #f6d21e;
    --text-light: #f0f0f0;
    --text-muted: #d7d7e4;
    --text-soft: #cfcfcf;
  }
  * { box-sizing: border-box; margin: 0; padding: 0; }
  html, body {
    width: 1125px; height: 1200px; overflow: hidden;
    background: var(--page);
    font-family: "Open Sans", Arial, sans-serif;
  }
  .canvas { position: relative; width: 1125px; height: 1200px; }
  .card {
    position: absolute; left: 150px; width: 826px;
    border-radius: 26px; overflow: hidden;
    background: linear-gradient(90deg, var(--card-dark) 0%, var(--card-dark) 70%, var(--card-dark-edge) 100%);
    box-shadow: 0 6px 14px rgba(0,0,0,.25);
  }
  .card--front { top: 98px; height: 470px; }
  .card--back { top: 631px; height: 472px; }

  .front-header {
    height: 286px; display: flex; align-items: center; justify-content: center;
  }
  .brand { display: flex; align-items: center; gap: 22px; }
  .brand-dot {
    width: 58px; height: 58px; border-radius: 50%;
    background: var(--accent-yellow);
  }
  .brand-name {
    font-size: 54px; font-weight: 600; letter-spacing: 3px;
    color: var(--text-light); line-height: 1;
  }
  .divider-line { height: 3px; background: var(--accent-yellow); }
  .contact-band {
    height: 181px;
    background: linear-gradient(90deg, var(--band-blue) 0%, var(--band-blue) 55%, var(--band-blue-deep) 100%);
    display: flex; align-items: center; padding-bottom: 14px;
  }
  .identity {
    width: 378px; text-align: right; color: var(--text-light);
  }
  .identity-name {
    font-size: 27px; font-weight: 600; color: var(--accent-yellow); line-height: 1.2;
  }
  .identity-role { font-size: 18px; line-height: 1.45; }
  .identity-address { font-size: 16.5px; line-height: 1.5; }
  .band-rule {
    width: 1px; height: 84px; background: rgba(255,255,255,.45); margin: 0 24px 0 26px;
  }
  .contact-list { list-style: none; color: var(--text-muted); font-size: 17.5px; line-height: 1.42; }
  .contact-item { display: flex; align-items: center; gap: 10px; }
  .contact-icon { width: 16px; height: 16px; flex: none; }

  .back-mark {
    position: absolute; left: 0; right: 0; top: 150px;
    display: flex; justify-content: center; align-items: center; gap: 20px;
  }
  .back-mark .brand-dot { width: 46px; height: 46px; }
  .back-mark .brand-name { font-size: 42px; }
  .services {
    position: absolute; left: 0; right: 0; top: 340px;
    text-align: center; font-style: italic; font-size: 17.5px;
    line-height: 1.45; color: var(--text-soft);
  }
</style>
</head>
<body>
<main class="canvas">
  <section class="card card--front">
    <header class="front-header">
      <div class="brand">
        <span class="brand-dot"></span>
        <span class="brand-name">MARTIN R. HALE</span>
      </div>
    </header>
    <div class="divider-line"></div>
    <div class="contact-band">
      <div class="identity">
        <p class="identity-name">Martin R.Hale</p>
        <p class="identity-role">Forensic document Examiner</p>
        <p class="identity-address">P.O.Box 2184, Ashford, OR 97410</p>
      </div>
      <div class="band-rule"></div>
      <ul class="contact-list">
        <li class="contact-item">
          <svg class="contact-icon" viewBox="0 0 16 16" aria-hidden="true"><path fill="#f6d21e" d="M3.6 1.2l2.3 2.6-1.2 1.9c.9 1.9 2.4 3.5 4.4 4.6l1.9-1.2 2.6 2.3-1.3 2.4C7.7 13.9 2.3 8.6 1.3 2.6z"/></svg>
          <span>(555) 210-4476</span>
        </li>
        <li class="contact-item">
          <svg class="contact-icon" viewBox="0 0 16 16" aria-hidden="true"><rect x="1" y="3.5" width="14" height="9.5" fill="#f6d21e"/><path d="M1.5 4l6.5 5 6.5-5" fill="none" stroke="#3232a0" stroke-width="1.3"/></svg>
          <span>mhale@quillmarkreview.info</span>
        </li>
        <li class="contact-item">
          <svg class="contact-icon" viewBox="0 0 16 16" aria-hidden="true"><circle cx="8" cy="8" r="7" fill="#f6d21e"/><path d="M4 4.5c1.5.5 2 1.8 1.2 3 .9.8 2 .3 2.2 1.9.1 1.3-.6 2.3 0 3.6M10 2.5c-.6 1.5.7 2 1.8 2.2.3 1.5-.8 2-.2 3.3.6 1 1.6.8 2.3.5" fill="none" stroke="#3232a0" stroke-width="1.2"/></svg>
          <span>www.quillmarkreview.info</span>
        </li>
      </ul>
    </div>
  </section>

  <section class="card card--back">
    <div class="back-mark">
      <span class="brand-dot"></span>
      <span class="brand-name">MARTIN R. HALE</span>
    </div>
    <p class="services">Full service laboratory, Specializing in handwriting comparisons,<br>obliterations, alterations, indented wrinting recovery, etc.</p>
  </section>
</main>
</body>
</html>
```